Business Card Design

New business card design

Target Market(s)

Residential & Commercial Property Managers

Industry/Entity Type

Plumbing Services

Contact Information for Business Card

Name - Rowan Keddle, title - Director, Phone Number - 0431 286 517, email - rowan@tbk-plumbing.com.au, Company ABN - 73 215 904 386,

Font styles to use
Sans Serif

Colors
0054AA
0677BA
7BADD7
CADEEF
E8F1F8

```html
<!DOCTYPE html>
<html lang="en">
<head>
<meta charset="utf-8">
<title>TBK Plumbing Services – Business Card</title>
<link rel="stylesheet" href="https://fonts.googleapis.com/css2?family=Arimo:wght@400;700&display=swap">
<style>
  :root {
    --backdrop: #9c9c9c;
    --card-white: #f6f6f6;
    --card-navy: #0d1224;
    --ink: #2b2f36;
    --ink-soft: #4a4e55;
    --accent: #00a9e8;
    --on-navy: #f2f4f8;
  }
  * { margin: 0; padding: 0; box-sizing: border-box; }
  html, body { width: 1200px; height: 1050px; overflow: hidden; }
  body {
    background: var(--backdrop);
    font-family: "Arimo", Arial, sans-serif;
    position: relative;
  }
  .card {
    position: absolute;
    left: 250px;
    width: 700px;
    height: 400px;
    border-radius: 22px;
    box-shadow: 0 6px 18px rgba(0,0,0,0.18);
  }
  .card--front { top: 90px; background: var(--card-white); }
  .card--back { top: 560px; background: var(--card-navy); }

  .brand {
    position: absolute;
    top: 58px;
    right: 56px;
    display: flex;
    align-items: center;
    gap: 12px;
  }
  .brand__dot {
    width: 16px; height: 16px;
    border-radius: 50%;
    background: var(--accent);
  }
  .brand__name {
    font-size: 30px;
    font-weight: 400;
    letter-spacing: 1px;
    color: var(--ink);
  }

  .contact {
    position: absolute;
    left: 56px;
    bottom: 56px;
  }
  .contact__name {
    font-size: 32px;
    font-weight: 700;
    color: var(--ink);
    line-height: 1.1;
  }
  .contact__title {
    font-size: 17px;
    color: var(--accent);
    margin-top: 2px;
  }
  .contact__details {
    margin-top: 28px;
    font-size: 17px;
    color: var(--ink-soft);
    white-space: nowrap;
  }
  .contact__sep { margin: 0 12px; }

  .back__brand {
    position: absolute;
    top: 140px;
    left: 0; right: 0;
    display: flex;
    justify-content: center;
    align-items: center;
    gap: 16px;
  }
  .back__dot {
    width: 44px; height: 44px;
    border-radius: 50%;
    background: var(--accent);
  }
  .back__name {
    font-size: 40px;
    font-weight: 400;
    color: var(--accent);
    letter-spacing: 1px;
  }
  .back__web {
    position: absolute;
    bottom: 70px;
    left: 0; right: 0;
    text-align: center;
    font-size: 18px;
    color: var(--on-navy);
    letter-spacing: 0.5px;
  }
</style>
</head>
<body>
  <section class="card card--front">
    <div class="brand">
      <span class="brand__dot"></span>
      <span class="brand__name">tbk plumbing services</span>
    </div>
    <div class="contact">
      <h1 class="contact__name">Rowan Keddle</h1>
      <p class="contact__title">Director</p>
      <p class="contact__details">ABN - 73 215 904 386<span class="contact__sep">|</span>0431 286 517<span class="contact__sep">|</span>rowan@tbk-plumbing.com.au</p>
    </div>
  </section>

  <section class="card card--back">
    <div class="back__brand">
      <span class="back__dot"></span>
      <span class="back__name">tbk plumbing services</span>
    </div>
    <p class="back__web">www.tbk-plumbing.com</p>
  </section>
</body>
</html>
```